Nur Briefpapier und VK für Pflegedienst, Logo vorhanden!!!!
Zielgruppe
Wir sind ein Pflegedienst, unsere Zielgruppe sind Krankenkassen und Patienten und andere Krankenhäuser mit denen wir zusammen arbeiten.
Aufgabenstellung
modern, seriös, elitär

```html
<!DOCTYPE html>
<html lang="de">
<head>
<meta charset="utf-8">
<title>Veldana Pflege – Geschäftsausstattung</title>
<link rel="stylesheet" href="https://fonts.googleapis.com/css2?family=Montserrat:wght@400;500;600&family=Arimo:wght@400&display=swap">
<style>
  :root {
    --brand-red: #e21e2b;
    --paper: #ffffff;
    --ink: #1d1d1f;
    --stage: #ffffff;
    --shadow: 0 3px 12px rgba(0,0,0,0.22);
  }
  * { box-sizing: border-box; margin: 0; padding: 0; }
  html, body { width: 1200px; height: 1200px; overflow: hidden; background: var(--stage); }
  .stage { position: relative; width: 1200px; height: 1200px; }

  .brand-mark {
    display: flex; align-items: center; gap: 5px;
    font-family: "Montserrat", sans-serif; font-weight: 600;
    color: var(--brand-red); white-space: nowrap;
  }
  .brand-mark .brand-square { width: 8px; height: 8px; background: currentColor; flex: none; }

  /* Business card front */
  .card-front {
    position: absolute; left: 43px; top: 304px; width: 350px; height: 200px;
    background: var(--paper); box-shadow: var(--shadow);
    font-family: "Montserrat", sans-serif; color: var(--ink);
  }
  .card-front .brand-mark { position: absolute; right: 20px; top: 22px; font-size: 12px; }
  .holder-name { position: absolute; left: 22px; top: 66px; font-size: 14px; font-weight: 500; letter-spacing: -0.2px; }
  .holder-role { position: absolute; left: 22px; top: 83px; font-size: 8px; color: var(--brand-red); }
  .contact-list { list-style: none; position: absolute; left: 22px; top: 98px; font-size: 10.5px; line-height: 14.5px; }
  .contact-list li { display: flex; align-items: center; gap: 6px; }
  .contact-list svg { width: 8px; height: 8px; fill: var(--brand-red); flex: none; }
  .corner-step { position: absolute; width: 17px; height: 17px; background: var(--brand-red); }
  .card-front .step-a { right: 0; bottom: 17px; }
  .card-front .step-b { right: 17px; bottom: 0; }

  /* Business card back */
  .card-back {
    position: absolute; left: 376px; top: 487px; width: 350px; height: 200px;
    background: var(--brand-red); box-shadow: var(--shadow); z-index: 2;
  }
  .card-back .brand-mark { position: absolute; left: 50%; top: 50%; transform: translate(-50%,-50%); color: #fff; font-size: 15px; }
  .card-back .notch { position: absolute; width: 17px; height: 17px; background: var(--stage); }
  .card-back .notch-a { left: 17px; top: 0; }
  .card-back .notch-b { left: 0; top: 17px; }

  /* Letterhead */
  .letterhead {
    position: absolute; left: 707px; top: 331px; width: 449px; height: 565px;
    background: var(--paper); box-shadow: var(--shadow); z-index: 1;
  }
  .letterhead .brand-mark { position: absolute; left: 66px; top: 88px; font-size: 17px; }
  .letter-corner { position: absolute; right: 0; top: 0; width: 48px; height: 48px; background: var(--brand-red); }
  .letter-corner::after { content: ""; position: absolute; left: 0; bottom: 0; width: 23px; height: 22px; background: var(--paper); }
  .letter-contacts {
    list-style: none; position: absolute; right: 41px; top: 40px;
    font-family: "Montserrat", sans-serif; font-size: 9px; line-height: 12.5px; color: var(--ink);
  }
  .letter-contacts li { display: flex; align-items: center; justify-content: flex-end; gap: 5px; }
  .letter-contacts svg { width: 7px; height: 7px; fill: var(--brand-red); }
  .letter-body {
    position: absolute; left: 43px; top: 182px; width: 365px;
    font-family: "Arimo", Arial, sans-serif; font-size: 9.9px; line-height: 11.7px;
    color: #111; text-align: justify;
  }
  .letter-body p + p { margin-top: 11.7px; }
  .letter-closing {
    position: absolute; right: 46px; top: 412px; text-align: right;
    font-family: "Arimo", Arial, sans-serif; font-size: 9.9px; color: #111;
  }
  .signature-area { width: 80px; height: 30px; margin: 4px 0 2px auto; background: linear-gradient(90deg, #f3f3f3, #e6e6e6); }
  .letter-closing .signer { display: block; text-align: center; padding-right: 12px; }
  .letter-band { position: absolute; left: 6px; bottom: 9px; width: 438px; height: 10px; background: var(--brand-red); }
</style>
</head>
<body>
<main class="stage">

  <section class="card-front" aria-label="Visitenkarte Vorderseite">
    <div class="brand-mark"><span class="brand-square"></span>Veldana</div>
    <div class="holder-name">OREN FALKNER</div>
    <div class="holder-role">OWNER</div>
    <ul class="contact-list">
      <li><svg viewBox="0 0 10 10"><path d="M2 0 4 2.5 3 4c.8 1.5 1.6 2.3 3 3L7.5 6 10 8 8.5 10C4 9.5.5 6 0 1.5Z"/></svg>+49 30 555 02 41 7</li>
      <li><svg viewBox="0 0 10 10"><rect x="2.5" y="0" width="5" height="10" rx="1"/></svg>+49 151 55 50 27 84</li>
      <li><svg viewBox="0 0 10 10"><path d="M0 2h10v6H0Z M0 2l5 3.5L10 2" /></svg>kontakt@veldana-post.de</li>
      <li><svg viewBox="0 0 10 10"><circle cx="5" cy="5" r="4.5" fill="none" stroke="#e21e2b" stroke-width="1"/><path d="M.5 5h9M5 .5v9" stroke="#e21e2b" stroke-width=".8"/></svg>www.veldana-pflege.de</li>
    </ul>
    <span class="corner-step step-a"></span>
    <span class="corner-step step-b"></span>
  </section>

  <section class="letterhead" aria-label="Briefbogen">
    <span class="letter-corner"></span>
    <div class="brand-mark"><span class="brand-square"></span>Veldana</div>
    <ul class="letter-contacts">
      <li><svg viewBox="0 0 10 10"><path d="M2 0 4 2.5 3 4c.8 1.5 1.6 2.3 3 3L7.5 6 10 8 8.5 10C4 9.5.5 6 0 1.5Z"/></svg>+49 30 555 02 41 7</li>
      <li><svg viewBox="0 0 10 10"><rect x="2.5" y="0" width="5" height="10" rx="1"/></svg>+49 151 55 50 27 84</li>
      <li><svg viewBox="0 0 10 10"><path d="M0 2h10v6H0Z"/></svg>kontakt@veldana-post.de</li>
      <li><svg viewBox="0 0 10 10"><circle cx="5" cy="5" r="4.5" fill="none" stroke="#e21e2b"/></svg>www.veldana-pflege.de</li>
    </ul>
    <div class="letter-body">
      <p>Lorem ipsum dolor sit amet, consectetur adipiscing elit. Aenean ut ipsum eget massa hendrerit vestibulum vel in velit. Donec pretium neque velit.</p>
      <p>Aliquam porta lectus nec mauris ornare venenatis. Vivamus non est turpis, et cursus sem. Mauris vehicula erat in diam auctor at bibendum nisl lacinia.</p>
      <p>Morbi imperdiet neque vehicula nunc convallis gravida. Vestibulum iaculis pretium placerat. Integer consequat, est sit amet facilisis eleifend, nibh nibh varius orci, eget dapibus arcu dui non purus. Pellentesque in magna mauris. Duis enim sapien, dictum vitae condimentum a, pulvinar vel lacus. Mauris et molestie nibh. Vestibulum vitae nulla at metus elementum porta sit amet interdum elit. Nulla sollicitudin neque eu nulla volutpat congue.</p>
      <p>Etiam pellentesque, velit id dapibus fermentum, turpis sapien ornare dui, ac tincidunt ligula odio congue purus. Nunc sed ante dui, in porta lectus. Cras nec sem lorem. In hac habitasse platea dictumst. Maecenas id diam quis dui porta tristique. Sed id egestas felis. Donec ullamcorper mattis posuere. Phasellus fermentum eleifend tortor vel dapibus. Vestibulum ante ipsum.</p>
    </div>
    <div class="letter-closing">
      Best Regards,
      <div class="signature-area" role="img" aria-label="Handschriftliche Unterschrift"></div>
      <span class="signer">Oren Falkner</span>
    </div>
    <span class="letter-band"></span>
  </section>

  <section class="card-back" aria-label="Visitenkarte Rückseite">
    <span class="notch notch-a"></span>
    <span class="notch notch-b"></span>
    <div class="brand-mark"><span class="brand-square"></span>Veldana</div>
  </section>

</main>
</body>
</html>
```